The Pale Serpent - Book two of the Varnel Saga

I would like a book cover design for use in self-publishing with BRN Publishing (Zelvora) a Science Fiction novel that is the second book in a trilogy.

In the first book, "The Ember Vow", Varnel Ostrikan, a Roman Centurian, is infused with The Ember Vow on the day of the crucifixion which makes him a tragic cursed anti-hero unable to be killed. Two thousand years later he is revived by and falls in love with Lena Faye Durst a beautiful archeologist student at Hallowmere University. They are drawn into a battle against a malevolent Artificial Intelligence named Veyra bent on the destruction of humanity. Veyra is destroyed but Varnel appears to have died from absorbing the energy of a nuclear bomb.

In the second book, The Pale Serpent, Veyra returns seeking revenge and targets Lena Faye Durst and her unborn child by kidnapping them. The birth of Dax, the son of The Ember Vow and Lena Faye Durst awakens Oru Melkesh, The Pale Serpent, who is foretold in Prophesy to be the destroyer of the world. The power in Varnel reawakens and he rescues Lena Faye. He then joins forces with Veyra to battle The Pale Serpent in an attempt to prevent the apocalypse.

Copy of the first book cover is included for reference

I have a subscription to Pixmerra and artwork from that source can be used in cover design.

The cover should be focused on The Pale Serpent, the apocalypse or the final battle between The Pale Serpent and Varnel.

The Prophesy and Oru Melkesh (The Pale Serpent), are inspired by the Zoroastrian end of world writings that were a precursor to the Bible's book of Revelations.

The Pale Serpent is a shape shifting beast that has multiple forms including that of a Dragon. His human form has a multi-headed dragon tattoo on his chest. He also has an axe wielding warrior Djinn form. The beast can mind control humans, is immensely strong, imperious to most physical attacks but when cut its blood becomes a weapon morphing into poison, acid, pestilence or stinging vermin.

I like the photo in Pixmerra 413982207 which I feel could work well as the front cover. I also like the concept in Pixmerra 5620391478 but do not like the artwork.

Target Market(s)

Adult male and female Science Fiction/Fantasy readers.

Industry/Entity Type

Science Fiction/Fantasy book

Requirements
Must have
• Dramatic art
Nice to have
• Potential concepts for cover: Focus on Pale Serpent character, focus on climatic battle between Pale Serpent and Varnel, fire, apocalyptic effect of final battle, The rear cover can be continuation of front or can focus on Varnel, Lena Faye Durst, Dax (the child) or the apocalypse.
Should not have
• comic art

```html
<!DOCTYPE html>
<html lang="en">
<head>
<meta charset="utf-8">
<title>The Pale Serpent – Book Two of the Varnel Saga</title>
<link rel="stylesheet" href="https://fonts.googleapis.com/css2?family=Cinzel:wght@400;500;600&family=Noticia+Text&display=swap">
<style>
  :root {
    --page: #141414;
    --cover-black: #050505;
    --ivory: #f3ead6;
    --gold: #d2a95e;
    --title-shadow: #6b5328;
    --body-text: #ece8e0;
    --scale-red: #a8412c;
    --head-red: #d8664a;
    --fire: #e59a45;
    --deep-red: #3a120c;
  }
  * { box-sizing: border-box; margin: 0; padding: 0; }
  html, body {
    width: 720px; height: 1200px; overflow: hidden;
    background: var(--page);
  }
  .cover-wrap {
    position: absolute; left: 14px; top: 350px;
    width: 692px; height: 500px;
    display: flex;
    background: var(--cover-black);
  }

  /* shared title */
  .title-block {
    font-family: "Cinzel", serif;
    font-weight: 400;
    color: var(--ivory);
    text-align: center;
    line-height: 0.86;
    text-shadow: 1px 1px 0 var(--title-shadow), 2px 2px 0 #3d2f15, 3px 3px 4px rgba(0,0,0,0.85);
  }
  .title-the { font-size: 26px; }
  .title-main { font-size: 56px; }
  .title-second { display: block; font-size: 50px; }
  .series-line {
    font-family: "Cinzel", serif;
    font-size: 10px; letter-spacing: 0.2px;
    color: var(--body-text);
    text-align: center;
  }

  /* back cover */
  .back-cover {
    position: relative; width: 326px; height: 100%;
    overflow: hidden;
  }
  .back-scenery {
    position: absolute; inset: 0;
    background:
      radial-gradient(ellipse 110% 30% at 45% 88%, rgba(78,52,22,0.6), transparent 72%),
      radial-gradient(ellipse 60% 25% at 30% 60%, rgba(40,30,18,0.45), transparent 75%),
      linear-gradient(180deg, #050505 0%, #090807 50%, #15100a 80%, #060505 100%);
  }
  .back-content { position: relative; padding-top: 44px; }
  .back-content .series-line { margin-top: 12px; }
  .blurb {
    margin: 18px 32px 0 37px;
    font-family: "Noticia Text", serif;
    font-size: 12px; line-height: 14.4px;
    color: var(--body-text);
    text-align: justify;
  }
  .blurb p + p { margin-top: 14px; }

  /* spine */
  .spine {
    position: relative; width: 40px; height: 100%;
    background: var(--cover-black);
  }
  .spine-title, .spine-author {
    position: absolute; left: 50%;
    font-family: "Cinzel", serif;
    white-space: nowrap;
    transform: translate(-50%, -50%) rotate(-90deg);
  }
  .spine-title { top: 178px; font-size: 21px; color: var(--gold); }
  .spine-author { top: 378px; font-size: 11px; color: var(--body-text); letter-spacing: 0.4px; }

  /* front cover */
  .front-cover {
    position: relative; width: 326px; height: 100%;
    overflow: hidden;
  }
  .front-art {
    position: absolute; inset: 0;
    background:
      radial-gradient(ellipse 22% 30% at 50% 46%, rgba(232,118,88,0.95), transparent 80%),
      radial-gradient(ellipse 42% 34% at 48% 38%, var(--head-red), rgba(160,56,36,0.75) 60%, transparent 85%),
      radial-gradient(ellipse 14% 34% at 82% 72%, rgba(18,12,10,0.9), transparent 80%),
      radial-gradient(ellipse 70% 12% at 35% 67%, rgba(240,168,80,0.9), transparent 80%),
      radial-gradient(ellipse 90% 20% at 45% 66%, rgba(200,110,45,0.75), transparent 85%),
      radial-gradient(ellipse 60% 40% at 85% 20%, rgba(120,40,26,0.85), transparent 80%),
      radial-gradient(ellipse 50% 40% at 10% 25%, rgba(130,46,30,0.85), transparent 80%),
      linear-gradient(180deg, #2a0e08 0%, #4e1a10 25%, #6a2a16 50%, #6e3b1a 62%, #1a110b 74%, #070605 84%, #040404 100%);
  }
  .front-author {
    position: absolute; top: 34px; left: 0; right: 0;
    text-align: center;
    font-family: "Cinzel", serif; font-weight: 500;
    font-size: 25px; color: var(--gold);
    text-shadow: 1px 1px 2px rgba(0,0,0,0.7);
  }
  .front-title { position: absolute; left: 0; right: 0; top: 362px; }
  .front-cover .series-line { position: absolute; left: 0; right: 0; top: 468px; }
</style>
</head>
<body>
  <main class="cover-wrap">
    <section class="back-cover">
      <div class="back-scenery" role="img" aria-label="Dark night scene with a faint forest silhouette lit by distant fire"></div>
      <div class="back-content">
        <h2 class="title-block">
          <span class="title-the">THE</span> <span class="title-main">PALE</span>
          <span class="title-second">SERPENT</span>
        </h2>
        <p class="series-line">BOOK TWO OF THE VARNEL SAGA</p>
        <div class="blurb">
          <p>The Pale Serpent, Veyra returns seeking revenge and targets Lena Faye Durst and her unborn child by kidnapping them. The birth of Dax, the son of the Ember Vow and Lena Faye Durst awakens Oru Melkesh, the Pale Serpent, who is foretold in Prophesy to be the destroyer of the world.</p>
          <p>The power in Varnel reawakens and he rescues Lena Faye. He then joins forces with Veyra to battle the Pale Serpent in an attempt to prevent the apocalypse.</p>
        </div>
      </div>
    </section>

    <section class="spine">
      <span class="spine-title">THE PALE SERPENT</span>
      <span class="spine-author">GRANT HOLLIS</span>
    </section>

    <section class="front-cover">
      <div class="front-art" role="img" aria-label="A horned red serpent-dragon looming over a burning landscape while a bare-backed warrior with a glowing sword stands on a rock facing it"></div>
      <p class="front-author">Grant Hollis</p>
      <h1 class="title-block front-title">
        <span class="title-the">THE</span> <span class="title-main">PALE</span>
        <span class="title-second">SERPENT</span>
      </h1>
      <p class="series-line">BOOK TWO OF THE VARNEL SAGA</p>
    </section>
  </main>
</body>
</html>
```